Parcelwise HQ letterhead and envelope

Design a formal (8.5x11) letterhead and envelope for sales outreach and legal matters. Using design input from https://www.parcelwisehq.example/ and the attached documents.

Industry/Entity Type

Software Service

Requirements
Must have
• These 4 hex colors are our official colors:
• #355c98 [blue]
• #1eb1a2 [teal]
• #fdba12 [gold]
• #f1653b [orange]
• So no other colors besides these should be used.

```html
<!DOCTYPE html>
<html lang="en">
<head>
<meta charset="utf-8">
<title>Parcelwise HQ Letterhead</title>
<link rel="stylesheet" href="https://fonts.googleapis.com/css2?family=Questrial&family=Arimo:wght@700&display=swap">
<style>
  :root {
    --brand-blue: #355c98;
    --ink: #3b3f46;
    --backdrop: #dde6f5;
    --paper: #ffffff;
  }
  html, body {
    margin: 0;
    width: 1200px;
    height: 893px;
    overflow: hidden;
    background: var(--backdrop);
  }
  .letterhead {
    position: absolute;
    left: 275px;
    top: 26px;
    width: 650px;
    height: 841px;
    background: var(--paper);
    box-shadow: 0 6px 24px rgba(53, 92, 152, 0.18);
    font-family: "Questrial", sans-serif;
    color: var(--ink);
  }
  .masthead {
    position: absolute;
    left: 60px;
    right: 60px;
    top: 46px;
    text-align: center;
  }
  .brand {
    display: inline-flex;
    align-items: center;
    gap: 12px;
    color: var(--brand-blue);
    font-size: 34px;
    letter-spacing: 0.5px;
  }
  .brand-dot {
    width: 34px;
    height: 34px;
    border: 3px solid var(--brand-blue);
    border-radius: 50%;
    box-sizing: border-box;
  }
  .masthead-rule {
    margin-top: 18px;
    border-top: 1.5px solid var(--brand-blue);
  }
  .contact-line {
    display: flex;
    justify-content: center;
    gap: 22px;
    margin-top: 8px;
    font-family: "Arimo", sans-serif;
    font-size: 11px;
    color: var(--brand-blue);
  }
  .contact-item {
    display: inline-flex;
    align-items: center;
    gap: 5px;
  }
  .contact-item svg { width: 12px; height: 12px; }
  .letter-body {
    position: absolute;
    left: 72px;
    right: 72px;
    top: 172px;
    font-size: 12px;
    line-height: 1.65;
  }
  .letter-body p { margin: 0 0 18px; }
  .signature {
    margin: 22px 8px 0 auto;
    width: max-content;
    text-align: left;
  }
  .signature-name { font-size: 16px; line-height: 1.2; }
  .signature-title { font-size: 10.5px; margin-top: 4px; line-height: 1.2; }
  .footer {
    position: absolute;
    left: 60px;
    right: 60px;
    bottom: 56px;
    text-align: center;
    font-family: "Arimo", sans-serif;
    color: var(--brand-blue);
  }
  .footer-web { font-size: 11px; letter-spacing: 4px; }
  .footer-address { font-size: 11px; margin-top: 6px; }
  .footer-rule { margin-top: 10px; border-top: 1.5px solid var(--brand-blue); }
</style>
</head>
<body>
<main class="letterhead">
  <header class="masthead">
    <div class="brand"><span class="brand-dot"></span><span class="brand-name">Parcelwise HQ</span></div>
    <div class="masthead-rule"></div>
    <div class="contact-line">
      <span class="contact-item">
        <svg viewBox="0 0 12 12" aria-hidden="true"><rect x="3" y="0.5" width="6" height="11" rx="1.2" fill="none" stroke="currentColor" stroke-width="1.4"/></svg>
        555 010-2468
      </span>
      <span class="contact-item">
        <svg viewBox="0 0 12 12" aria-hidden="true"><path d="M2 2.5c0 4 3.5 7.5 7.5 7.5l1-2-2.2-1-1 1C6 7.4 4.6 6 4 4.7l1-1L4 1.5z" fill="currentColor"/></svg>
        555 013 5790
      </span>
      <span class="contact-item">
        <svg viewBox="0 0 12 12" aria-hidden="true"><rect x="0.7" y="2.2" width="10.6" height="7.6" rx="1" fill="none" stroke="currentColor" stroke-width="1.3"/><path d="M1 3l5 4 5-4" fill="none" stroke="currentColor" stroke-width="1.2"/></svg>
        jdoe@parcelwisehq.example
      </span>
    </div>
  </header>

  <section class="letter-body">
    <p>Lorem ipsum dolor sit amet, consectetur adipiscing elit. Donec orci purus, luctus vitae dignissim eu, iaculis sed purus. Vivamus faucibus, ipsum nec aliquet viverra, leo mauris condimentum ligula, sit amet sagittis enim ligula quis arcu. Nam egestas tortor id nisi porttitor mattis. In tortor ante, ultricies in suscipit a, tempus non massa. Vivamus et auctor mi. Fusce vel massa nulla. Phasellus nec eros mauris, et scelerisque orci. Donec malesuada orci vitae nulla accumsan porta a id massa.</p>
    <p>Quisque accumsan iaculis magna sit amet fringilla. Maecenas consequat, magna eget tincidunt semper, odio nibh rutrum mi, id feugiat ante nisi eu risus. Vestibulum nunc orci, rhoncus a placerat in, ultricies in mi. Cras mattis varius eros, vel fringilla nisi suscipit eget. Quisque scelerisque sagittis nulla at porttitor. Mauris a justo et tellus interdum tristique. Sed id augue vitae urna euismod commodo aliquet a quam. Pellentesque arcu velit, cursus et malesuada ut, consequat et diam. Nullam erat sem, rhoncus id ullamcorper vitae, rhoncus et arcu. In ultricies ultricies nulla.</p>
    <p>Ut rutrum nisi iaculis at. Donec eu magna a metus ornare faucibus. Fusce aliquet faucibus ultricies. Morbi semper, est id tincidunt gravida, sem arcu adipiscing lacus, ac bibendum nulla leo eu purus. Quisque nec diam sed risus consectetur a accumsan quis quis nibh. Vestibulum id purus lorem. Donec eu magna a metus ornare faucibus. Fusce aliquet faucibus ultricies. Morbi semper, est id tincidunt gravida, sem arcu adipiscing lacus, ac bibendum nulla leo eu purus. Quisque nec diam sed risus consectetur a accumsan quis quis nibh. Vestibulum id purus lorem.</p>
    <div class="signature">
      <div class="signature-name">Owen Marlow</div>
      <div class="signature-title">Co-Founder &amp; CEO</div>
    </div>
  </section>

  <footer class="footer">
    <div class="footer-web">www.parcelwisehq.example</div>
    <div class="footer-address">42 Harbor Lane NE, Suite C-7, Riverton, ST 00000</div>
    <div class="footer-rule"></div>
  </footer>
</main>
</body>
</html>
```